Velora Reggaeton Night

I'd like to create a flyer / poster for a reaggaeton Xmas party in London. The party will be titled "Velora" and will be VIP for friends of friends only. The concept has to remain classy and stylish as I don't want it to be related to anything tropical at first glance. People attending the party will be a bit up-scale so the style is key. I am thinking of a black background and golden or silver letters, which give a bit of a "bling" look. Since the party will take place in Central London, I was thinking perhaps including something that relates to the city (St. Wendel's Cathedral, the Quillon, etc.). I have seen a few ideas and I am happy to send those over to illustrate a bit better what I am thinking of. Color wise, the theme could be very black and grey (for the London buildings) and only keep a few bright red colors if including London double decker buses or phone booths. Need to include something that gives the poster / flyer a Latin vibe as well.

Target Market(s)

25-35 year olds. Young professionals living in London. Latin American and European origins. People that enjoy dancing and like reggaeton music in particular.

Industry/Entity Type

Latin American Café

Requirements
Must have
• Must have the name of the party, VELORA, as a big part of the flyer. Also the words "reggaeton party" or "reggaeton night". Something catchy. The date will be December 16 2017. Time will be 7pm to 3am. Location is Central London (Bank). I don't want to specify the location as I want it to be "secret" and only people with the ticket will be given the address.
Nice to have
• Nice to have something that resembles London but also the Latin, bling vibe of reggaeton music. Velora means "flirt" in Spanish so I want the design to be flirty but elegant and very stylish. VELORA could be written in Gold or Silver to make it stand-out. Could be made up of yellow light bulbs as well. And could include a rose to make it more flirty. See examples attached.
Should not have
• Typical tropical or Cuban type designs. I don't want anything too colorful as I want to keep it classy and stylish. Try to avoid people dancing in the flyer. Don't want a photo of sexy women in the flyer. Need to keep it classy.

```html
<!DOCTYPE html>
<html lang="en">
<head>
<meta charset="utf-8">
<title>Velora Reggaeton Night</title>
<link rel="stylesheet" href="https://fonts.googleapis.com/css2?family=Josefin+Sans:wght@600;700&family=Oswald:wght@400;500&family=Great+Vibes&display=swap">
<style>
:root{
  --page:#ffffff;
  --black:#050302;
  --white:#fbf6f1;
  --copper:#e9a784;
  --copper-deep:#8a4a2c;
  --line:#7a3a22;
}
*{margin:0;padding:0;box-sizing:border-box}
html,body{width:1200px;height:1200px;overflow:hidden;background:var(--page)}
.poster{position:absolute;left:232px;top:32px;width:792px;height:1160px;overflow:hidden;background:var(--black)}
.layer{position:absolute;left:0;top:0;width:792px;height:1160px}
.fireworks{position:absolute;left:0;top:0;width:792px;height:640px;
  background:radial-gradient(ellipse 360px 320px at 430px 230px,rgba(214,222,60,.55),rgba(120,130,20,.22) 55%,transparent 82%)}
.skyline{position:absolute;
  background:linear-gradient(180deg,rgba(233,167,132,0) 0%,rgba(233,167,132,.14) 40%,rgba(233,167,132,.24) 100%)}
.skyline-left{left:16px;top:440px;width:136px;height:262px}
.skyline-right{left:636px;top:448px;width:140px;height:258px}
.txt{position:absolute;white-space:nowrap;color:var(--white);line-height:1}
.title{left:0;width:792px;text-align:center;top:610px;font-family:"Josefin Sans",sans-serif;font-weight:700;font-size:92px;letter-spacing:2px;
  text-shadow:0 0 2px #000,3px 3px 0 #3a2418}
.city{left:174px;top:698px;font-family:"Josefin Sans",sans-serif;font-weight:700;font-size:46px;letter-spacing:1px;
  text-shadow:2px 2px 0 #3a2418}
.script{font-family:"Great Vibes",cursive;fill:var(--copper)}
.rule{position:absolute;left:10px;width:772px;height:2px;background:linear-gradient(90deg,transparent,var(--line) 20%,var(--copper-deep) 50%,var(--line) 80%,transparent)}
.time{left:0;width:792px;text-align:center;top:896px;font-family:"Oswald",sans-serif;font-weight:500;font-size:54px;transform:scaleX(.78)}
.date{left:0;width:792px;text-align:center;font-family:"Josefin Sans",sans-serif;font-weight:700;font-size:48px;letter-spacing:1px}
.date-day{top:963px}
.date-full{top:1007px}
.date-full sup{font-size:25px;vertical-align:18px;line-height:0}
.small{left:0;width:792px;text-align:center;font-family:"Oswald",sans-serif;font-weight:400}
.venue{top:1068px;font-size:21px;letter-spacing:4px}
.handle{top:1098px;font-size:26px;letter-spacing:4px}
</style>
</head>
<body>
<div class="poster">
  <div class="fireworks" role="img" aria-label="Golden fireworks bursting in the night sky"></div>
  <svg class="layer artwork" viewBox="0 0 792 1160" aria-hidden="true">
    <defs>
      <linearGradient id="lime-fade" x1="0" y1="0" x2="0" y2="1">
        <stop offset="0" stop-color="#c9cf2e"/>
        <stop offset="1" stop-color="#a8a028"/>
      </linearGradient>
      <linearGradient id="amber" x1="0" y1="0" x2="0" y2="1">
        <stop offset="0" stop-color="#9c9a22"/>
        <stop offset="1" stop-color="#c7a53a"/>
      </linearGradient>
      <linearGradient id="glitter" x1="0" y1="0" x2="0" y2="1">
        <stop offset="0" stop-color="#6e5a2e"/>
        <stop offset="1" stop-color="#2c2214"/>
      </linearGradient>
      <linearGradient id="slate" x1="0" y1="0" x2="0" y2="1">
        <stop offset="0" stop-color="#241d1a"/>
        <stop offset="1" stop-color="#4a3a33"/>
      </linearGradient>
      <linearGradient id="lower-dark" x1="0" y1="0" x2="0" y2="1">
        <stop offset="0" stop-color="#0a0804"/>
        <stop offset="1" stop-color="#3a2a12"/>
      </linearGradient>
    </defs>
    <g class="facets" opacity=".3">
      <polygon points="0,0 300,0 150,300" fill="#3e4412"/>
      <polygon points="492,0 792,0 642,300" fill="#3e4412"/>
      <polygon points="80,200 300,200 190,430" fill="#4a5214"/>
      <polygon points="492,200 712,200 602,430" fill="#4a5214"/>
    </g>
    <polygon class="apex-large" points="396,108 616,596 176,596" fill="url(#amber)"/>
    <polygon class="apex-lower" points="263,404 529,404 616,596 176,596" fill="url(#lower-dark)"/>
    <polygon class="band-dark" points="282,360 510,360 529,404 263,404" fill="#050302"/>
    <polygon class="apex-glitter" points="396,108 524,324 268,324" fill="#1a1608"/>
    <polygon class="apex-inner" points="396,212 472,324 320,324" fill="url(#lime-fade)"/>
    <polygon class="inverted-glitter" points="240,432 556,432 408,600" fill="url(#glitter)"/>
    <polygon class="apex-small" points="396,520 448,592 344,592" fill="#d7a45a" opacity=".85"/>
    <polygon class="title-base" points="112,836 684,836 398,512" fill="url(#slate)"/>
    <rect class="title-plate" x="152" y="600" width="484" height="100" fill="#050302"/>
  </svg>
  <div class="skyline skyline-left" role="img" aria-label="Line drawing of London skyline with observation wheel and old buildings"></div>
  <div class="skyline skyline-right" role="img" aria-label="Line drawing of London skyline with clock tower and curved glass tower"></div>

  <div class="txt title">VELORA</div>
  <div class="txt city">LONDON</div>
  <svg class="layer script-layer" viewBox="0 0 792 1160">
    <text class="script" x="180" y="836" font-size="112" textLength="434" lengthAdjust="spacingAndGlyphs" transform="rotate(-14.5 180 836)">Reggaeton</text>
    <text class="script" x="360" y="872" font-size="125" textLength="288" lengthAdjust="spacingAndGlyphs" transform="rotate(-13.5 360 872)">Night</text>
  </svg>

  <div class="rule" style="top:852px"></div>
  <div class="txt time">7PM - 3AM</div>
  <div class="rule" style="top:958px"></div>
  <div class="txt date date-day">SATURDAY</div>
  <div class="txt date date-full">DECEMBER 16<sup>TH</sup> 2017</div>
  <div class="rule" style="top:1055px"></div>
  <div class="txt small venue">CENTRAL LONDON</div>
  <div class="txt small handle">FOLLOW US @VELORALONDON</div>
</div>
</body>
</html>
```